Ward Compass Business Card Design*

We need a business card design for our company Ward Compass. Our company is specialized in providing online consulting services regarding medical institutions, hospitals and doctors. We work with patients worldwide looking to choose between healthcare providers. We have a website you may use as a reference, where we list doctors and clinics worldwide. So we target Medical providers as well as patients worldwide.
Target Market(s)
Medical Providers and patients around the world
Industry/Entity Type
Medical
Contact Information for Business Card
Salwa Kettani
CEO
+90 612 348 2175
info@wardcompass.example
www.wardcompass.example
14 Annakhil 7 H.R.B. Rabat, Morocco
Requirements
Must have
- Company logo/name on one full side, personal info and smaller logo and company name on the other side.
Nice to have
- Smart and elegant design

```html
<!DOCTYPE html>
<html lang="en">
<head>
<meta charset="UTF-8">
<title>Ward Compass Business Card</title>
<link href="https://fonts.googleapis.com/css2?family=Montserrat:wght@300;400;600;700&display=swap" rel="stylesheet">
<style>
  :root{
    --navy:#1d3a6e;
    --grey:#6f6f71;
    --light-grey:#9a9a9c;
    --card:#ffffff;
    --stage:#e6e7ea;
    --ink:#2a2a2c;
  }
  *{box-sizing:border-box;margin:0;padding:0}
  html,body{width:1200px;height:900px;overflow:hidden}
  body{background:var(--stage);font-family:"Montserrat",sans-serif;position:relative}
  .card{
    position:absolute;left:285px;width:630px;height:360px;
    background:var(--card);box-shadow:0 10px 28px rgba(0,0,0,.18);overflow:hidden;
  }
  .card--front{top:50px}
  .card--back{top:490px}
  .card__band{position:absolute;left:0;bottom:0;width:630px;height:40px}
  .brand{position:absolute;display:flex;align-items:center}
  .brand__dot{border-radius:50%;background:var(--navy);flex:none}
  .brand__name{font-weight:700;color:var(--navy);letter-spacing:.02em;white-space:nowrap}
  .card--front .brand{left:110px;top:125px;gap:22px}
  .card--front .brand__dot{width:64px;height:64px}
  .card--front .brand__name{font-size:40px}
  .website{
    position:absolute;left:280px;top:262px;font-size:13px;font-weight:600;
    letter-spacing:.28em;color:var(--navy);
  }
  .card--back .brand{left:150px;top:100px;gap:16px}
  .card--back .brand__dot{width:46px;height:46px}
  .card--back .brand__name{font-size:29px}
  .person{position:absolute;left:150px;top:230px;text-align:right;width:175px}
  .person__name{font-size:17px;letter-spacing:.02em;white-space:nowrap}
  .person__first{font-weight:700;color:var(--navy)}
  .person__last{font-weight:300;color:var(--light-grey)}
  .person__role{font-size:10px;font-weight:600;color:var(--ink);margin-top:2px}
  .divider{
    position:absolute;left:350px;top:200px;width:2px;height:80px;
    background:linear-gradient(to bottom,rgba(29,58,110,0),var(--navy) 50%,rgba(29,58,110,0));
  }
  .contact{position:absolute;left:375px;top:210px;list-style:none}
  .contact__item{display:flex;align-items:center;gap:10px;font-size:13px;color:var(--ink);margin-bottom:10px;white-space:nowrap}
  .contact__icon{width:16px;height:16px;flex:none}
</style>
</head>
<body>

<section class="card card--front">
  <div class="brand">
    <span class="brand__dot"></span>
    <span class="brand__name">WARD COMPASS</span>
  </div>
  <p class="website">www.wardcompass.example</p>
  <svg class="card__band" viewBox="0 0 630 40" aria-hidden="true">
    <rect x="0" y="28" width="630" height="12" fill="var(--navy)"/>
    <path d="M470 40 V30 Q470 6 500 6 H630 V40 Z" fill="var(--grey)"/>
  </svg>
</section>

<section class="card card--back">
  <div class="brand">
    <span class="brand__dot"></span>
    <span class="brand__name">WARD COMPASS</span>
  </div>
  <div class="person">
    <p class="person__name"><span class="person__first">SALWA</span> <span class="person__last">KETTANI</span></p>
    <p class="person__role">CEO</p>
  </div>
  <div class="divider"></div>
  <ul class="contact">
    <li class="contact__item">
      <svg class="contact__icon" viewBox="0 0 16 16" aria-hidden="true"><path d="M1 5 Q8 0 15 5 L13 7 L11 5.5 L5 5.5 L3 7 Z M3 8 H13 L14 14 H2 Z" fill="var(--navy)"/><circle cx="8" cy="11" r="1.6" fill="#fff"/></svg>
      <span>+90 612 348 2175</span>
    </li>
    <li class="contact__item">
      <svg class="contact__icon" viewBox="0 0 16 16" aria-hidden="true"><rect x="1" y="3" width="14" height="10" fill="var(--navy)"/><path d="M1 3 L8 9 L15 3" fill="none" stroke="#fff" stroke-width="1.2"/></svg>
      <span>info@wardcompass.example</span>
    </li>
  </ul>
  <svg class="card__band" viewBox="0 0 630 40" aria-hidden="true">
    <rect x="0" y="28" width="630" height="12" fill="var(--navy)"/>
    <path d="M470 40 V30 Q470 6 500 6 H630 V40 Z" fill="var(--grey)"/>
  </svg>
</section>

</body>
</html>
```